BRISKLY sparkling water needs new artwork! Based in Southern California

"Briskly" is a new sparkling water company based in Southern California that offers refreshing flavors (lime, cherry, & mango) with B vitamins and antioxidants.

We would like to see packaging designs for standard 12oz cans for each of the three flavors.
Our initial preference is to have individual artwork for each flavor.

Attached are examples of competitors' designs.
Updates

We are extending the deadline for the Thanksgiving Holiday. Thank you all for your contributions.

```html
<!DOCTYPE html>
<html lang="en">
<head>
<meta charset="utf-8">
<title>Briskly Sparkling Water – 12oz Can Label Templates</title>
<link rel="stylesheet" href="https://fonts.googleapis.com/css2?family=Lato:wght@300;400;700&family=Montserrat:ital,wght@0,400;0,500;0,700;0,800;1,800&display=swap">
<style>
  :root{
    --guide:#9a86c6;
    --paper:#ffffff;
    --ink:#1d1d1b;
    --cherry-bg:#fdf0f3; --cherry-brand:#e4005a;
    --cherry-w1:#f5b0bd; --cherry-w2:#ea5d78; --cherry-w3:#e2004f; --cherry-w4:#a5003b; --cherry-fruit:#e3262b;
    --lime-bg:#f7f6e2; --lime-brand:#5daf38;
    --lime-w1:#8cc23a; --lime-w2:#74a828; --lime-w3:#8cc23a; --lime-w4:#609422; --lime-fruit:#c6e07a;
    --mango-bg:#f8f6e2; --mango-brand:#f39a12;
    --mango-w1:#f9c51c; --mango-w2:#fde04a; --mango-w3:#f9c51c; --mango-w4:#fde64f; --mango-fruit:#f6b417;
  }
  *{margin:0;padding:0;box-sizing:border-box}
  html,body{width:1200px;height:2332px;overflow:hidden;background:var(--paper)}
  body{position:relative;font-family:"Montserrat",sans-serif;color:var(--ink)}
  .template{position:absolute;left:0;width:1200px;height:773px}
  .template--cherry{top:0;--bg:var(--cherry-bg);--brand:var(--cherry-brand);--w1:var(--cherry-w1);--w2:var(--cherry-w2);--w3:var(--cherry-w3);--w4:var(--cherry-w4);--fruit:var(--cherry-fruit)}
  .template--lime{top:783px;--bg:var(--lime-bg);--brand:var(--lime-brand);--w1:var(--lime-w1);--w2:var(--lime-w2);--w3:var(--lime-w3);--w4:var(--lime-w4);--fruit:var(--lime-fruit)}
  .template--mango{top:1562px;--bg:var(--mango-bg);--brand:var(--mango-brand);--w1:var(--mango-w1);--w2:var(--mango-w2);--w3:var(--mango-w3);--w4:var(--mango-w4);--fruit:var(--mango-fruit)}
  .artwork{position:absolute;left:0;top:0;width:1200px;height:773px}
  .overlay{pointer-events:none}
  .bg{fill:var(--bg)}
  .wave-1{fill:var(--w1)} .wave-2{fill:var(--w2)} .wave-3{fill:var(--w3)} .wave-4{fill:var(--w4)}
  .fruit{fill:var(--fruit);opacity:.85}
  .guide-line{stroke:var(--guide);stroke-width:.9;fill:none}
  .guide-dash{stroke:var(--guide);stroke-width:1.2;stroke-dasharray:9 6;fill:none}
  .guide-thin{stroke:var(--guide);stroke-width:.5;fill:none;opacity:.8}
  .panel-box{fill:#fff;stroke:#555;stroke-width:.8}
  .panel-caption{font-family:"Montserrat",sans-serif;font-size:6px;font-weight:700;fill:var(--ink)}
  .guide-text{position:absolute;font-family:"Lato",sans-serif;font-weight:400;color:var(--guide);font-size:11px;white-space:nowrap;line-height:1.1}
  .template-title{position:absolute;left:0;width:1200px;top:89px;text-align:center;font-family:"Lato",sans-serif;font-size:25px;color:var(--guide);font-weight:400}
  .transitional{position:absolute;left:1035px;top:140px;font-family:"Lato",sans-serif;color:var(--guide)}
  .transitional strong{display:block;font-size:12.5px;font-weight:700}
  .transitional span{display:block;font-size:8.5px}
  .dim-label{position:absolute;left:520px;width:136px;text-align:center;background:#fff;font-family:"Lato",sans-serif;color:var(--guide);font-size:11.5px;line-height:14px}
  .centered{text-align:center}
  .back-copy{position:absolute;left:204px;top:310px;width:175px;font-size:6.6px;line-height:9.4px;text-align:center;color:#333;white-space:nowrap}
  .brand-name{position:absolute;left:390px;width:394px;top:310px;text-align:center;font-size:52px;font-weight:700;color:var(--brand);letter-spacing:1px;line-height:60px}
  .product-name{position:absolute;left:390px;width:394px;top:389px;text-align:center;font-size:22px;font-weight:500;letter-spacing:1.5px;line-height:24px}
  .divider{position:absolute;left:557px;top:442px;width:46px;height:2px;background:var(--brand)}
  .claims{position:absolute;left:390px;width:394px;top:452px;text-align:center;font-size:10.5px;line-height:14px;font-weight:400}
  .flavor-pill{position:absolute;left:550px;top:488px;width:80px;height:16px;border-radius:8px;background:var(--brand);color:#fff;font-size:11px;font-weight:700;letter-spacing:2.5px;text-align:center;line-height:16px}
  .volume{position:absolute;left:390px;width:394px;top:638px;text-align:center;color:#fff;font-size:17px;font-weight:500;line-height:20px}
  .claim-icon{position:absolute;left:812px;width:28px;height:28px;border-radius:50%;border:1.6px solid var(--brand);color:var(--brand);text-align:center;font-weight:700;background:#fff}
  .claim-icon b{display:block;font-size:10px;line-height:12px;margin-top:3px}
  .claim-icon small{display:block;font-size:3.6px;line-height:4px;font-weight:700}
  .claim-icon--word{font-size:5px;line-height:6px;padding-top:7px}
  .claim-icon--single{padding-top:10px}
  .nutrition-label{position:absolute;left:857px;top:321px;font-size:6.5px;font-weight:700}
  .boost{position:absolute;left:861px;top:480px;width:64px;height:64px;border-radius:50%;border:2.5px solid var(--brand);text-align:center;color:var(--brand);font-weight:800;font-style:italic;font-size:11px;line-height:12px;padding-top:18px;background:#fff}
</style>
</head>
<body>

<!-- ===== Cherry ===== -->
<section class="template template--cherry">
  <svg class="artwork" viewBox="0 0 1200 773">
    <defs>
      <clipPath id="clip-cherry"><rect x="183" y="219" width="828" height="456"/><rect x="397" y="183" width="401" height="503"/></clipPath>
    </defs>
    <g clip-path="url(#clip-cherry)">
      <rect class="bg" x="183" y="183" width="828" height="503"/>
      <path class="wave-1" d="M183 550 C250 532 320 558 400 544 S560 528 640 546 S820 528 1011 542 V686 H183Z"/>
      <path class="wave-2" d="M183 572 C260 562 330 582 420 570 S580 558 660 576 S830 560 1011 570 V686 H183Z"/>
      <path class="wave-3" d="M183 594 C270 584 340 604 430 592 S600 580 680 598 S840 582 1011 592 V686 H183Z"/>
      <path class="wave-4" d="M183 616 C260 608 350 626 440 614 S610 604 700 620 S850 606 1011 616 V638 C850 630 700 644 600 634 S380 642 183 636Z"/>
      <g role="img" aria-label="Scattered cherry illustrations">
        <circle class="fruit" cx="232" cy="287" r="13"/><circle class="fruit" cx="300" cy="290" r="13"/>
        <circle class="fruit" cx="460" cy="292" r="16"/><circle class="fruit" cx="612" cy="295" r="15"/>
        <circle class="fruit" cx="765" cy="287" r="16"/><circle class="fruit" cx="406" cy="397" r="14"/>
        <circle class="fruit" cx="782" cy="381" r="16"/><circle class="fruit" cx="740" cy="447" r="15"/>
        <circle class="fruit" cx="483" cy="537" r="16"/><circle class="fruit" cx="723" cy="577" r="15"/>
        <circle class="fruit" cx="325" cy="584" r="12"/><circle class="fruit" cx="898" cy="287" r="13"/>
        <circle class="fruit" cx="970" cy="287" r="12"/><circle class="fruit" cx="962" cy="577" r="12"/>
      </g>
    </g>
    <rect class="guide-line" x="183" y="219" width="828" height="456"/>
    <rect class="guide-thin" x="187" y="226" width="806" height="442"/>
    <rect class="guide-line" x="397" y="183" width="401" height="503"/>
    <line class="guide-dash" x1="159" y1="272" x2="1036" y2="272"/>
    <line class="guide-line" x1="111" y1="222" x2="158" y2="222"/><line class="guide-line" x1="111" y1="227" x2="158" y2="227"/>
    <line class="guide-line" x1="1026" y1="222" x2="1073" y2="222"/><line class="guide-line" x1="1026" y1="227" x2="1073" y2="227"/>
    <line class="guide-line" x1="113" y1="668" x2="160" y2="668"/><line class="guide-line" x1="113" y1="673" x2="160" y2="673"/>
    <line class="guide-line" x1="1031" y1="668" x2="1078" y2="668"/><line class="guide-line" x1="1031" y1="673" x2="1078" y2="673"/>
    <line class="guide-line" x1="185" y1="159" x2="185" y2="214"/><line class="guide-thin" x1="190" y1="159" x2="190" y2="702"/>
    <line class="guide-line" x1="991" y1="159" x2="991" y2="214"/><line class="guide-thin" x1="993" y1="159" x2="993" y2="702"/>
    <line class="guide-line" x1="187" y1="682" x2="187" y2="724"/><line class="guide-line" x1="1010" y1="682" x2="1010" y2="724"/>
    <line class="guide-line" x1="189" y1="701" x2="1008" y2="701"/>
    <path class="guide-line" d="M194 697 L189 701 L194 705 M1003 697 L1008 701 L1003 705"/>
    <line class="guide-line" x1="1045" y1="173" x2="1004" y2="221"/><circle cx="1045" cy="173" r="2.2" fill="var(--guide)"/>
    <path class="guide-line" d="M1004 221 l7 -2 M1004 221 l1 -7"/>
  </svg>
  <h1 class="template-title">109 mm LF_4.875”_Template</h1>
  <span class="guide-text" style="left:162px;top:142px">1 mm clear</span>
  <span class="guide-text" style="left:972px;top:142px">5 mm clear</span>
  <div class="transitional"><strong>Transitional Area</strong><span>(transitions from sidewall to neck)</span></div>
  <span class="guide-text" style="left:577px;top:160px">109 mm LF</span>
  <span class="guide-text" style="left:47px;top:218px">2 mm clear</span>
  <span class="guide-text" style="left:1079px;top:218px">2 mm clear</span>
  <span class="guide-text" style="left:49px;top:665px">2 mm clear</span>
  <span class="guide-text" style="left:1084px;top:665px">2 mm clear</span>
  <span class="guide-text" style="left:1030px;top:419px;font-size:12px;line-height:15px">4.875” Cut Height<br>123.825 MM</span>
  <div class="dim-label" style="top:694px">225 MM SLIT WIDTH<br>8.8583”</div>
  <span class="guide-text centered" style="left:183px;top:735px;font-size:8.5px">1mm Bkgd Bleed<br>Overlap</span>
  <span class="guide-text centered" style="left:905px;top:718px;font-size:8.5px">2mm Bkgd Only<br>No Text/Art</span>

  <p class="back-copy">Lorem ipsum dolor sit amet, consectetuer<br>adipiscing elit. Aenean commodo ligula<br>eget dolor. Aenean massa. Cum sociis<br>natoque penatibus et magnis dis parturient<br>montes, nascetur ridiculus mus. Donec<br>quam felis, ultricies nec, pellentesque eu,<br>pretium quis, sem. Nulla consequat massa<br>quis enim. Donec pede justo, fringilla vel,<br>aliquet nec, vulputate eget, arcu. In enim<br>justo, rhoncus ut, imperdiet a, venenatis<br>vitae, justo. Nullam dictum felis eu pede<br>mollis pretium. Integer tincidunt. Cras<br>dapibus. Vivamus elementum semper nisi.<br>Aenean vulputate eleifend tellus. Aenean<br>leo ligula, porttitor eu, consequat vitae,<br>eleifend ac, enim. Aliquam lorem ante,<br>dapibus in, viverra quis, feugiat a, tellus.<br>Phasellus viverra nulla ut metus varius<br>laoreet. Quisque rutrum. Aenean imperdiet.<br>Etiam ultricies nisi vel augue. Curabitur<br>ullamcorper ultricies nisi. Nam eget dui.<br>Etiam rhoncus. Maecenas tempus, tellus</p>
  <div class="brand-name">Briskly</div>
  <div class="product-name">SPARKLING<br>WATER</div>
  <div class="divider"></div>
  <div class="claims">NATURAL FLAVORS<br>&amp; B-VITAMINS</div>
  <div class="flavor-pill">CHERRY</div>
  <div class="volume">12oz</div>

  <div class="claim-icon" style="top:295px"><b>0</b><small>SUGAR</small></div>
  <div class="claim-icon" style="top:327px"><b>0</b><small>CALORIES</small></div>
  <div class="claim-icon" style="top:361px"><b>0</b><small>SODIUM</small></div>
  <div class="claim-icon claim-icon--word" style="top:395px">B6 &amp;<br>B12</div>
  <div class="claim-icon claim-icon--word" style="top:430px">NON<br>GMO</div>
  <div class="claim-icon claim-icon--word" style="top:461px">GLUTEN<br>FREE</div>
  <div class="claim-icon claim-icon--word claim-icon--single" style="top:498px">VEGAN</div>
  <svg class="artwork overlay" viewBox="0 0 1200 773" aria-hidden="true">
    <rect class="panel-box" x="852" y="314" width="79" height="154"/>
    <rect class="panel-box" x="934" y="395" width="46" height="73"/>
    <text class="panel-caption" transform="translate(959 445) rotate(-90)">BARCODE</text>
  </svg>
  <span class="nutrition-label">NUTRITION PANEL</span>
  <div class="boost">BOOST<br>IMMUNITY</div>
</section>

<!-- ===== Lime ===== -->
<section class="template template--lime">
  <svg class="artwork" viewBox="0 0 1200 773">
    <defs>
      <clipPath id="clip-lime"><rect x="183" y="219" width="828" height="456"/><rect x="397" y="183" width="401" height="503"/></clipPath>
    </defs>
    <g clip-path="url(#clip-lime)">
      <rect class="bg" x="183" y="183" width="828" height="503"/>
      <path class="wave-1" d="M183 548 C250 530 320 556 400 542 S560 526 640 544 S820 526 1011 540 V686 H183Z"/>
      <path class="wave-2" d="M183 572 C260 562 330 582 420 570 S580 558 660 576 S830 560 1011 570 V592 C830 584 660 600 560 590 S330 600 183 594Z"/>
      <path class="wave-4" d="M183 610 C260 602 350 620 440 608 S610 598 700 614 S850 600 1011 610 V632 C850 624 700 638 600 628 S380 636 183 630Z"/>
      <g role="img" aria-label="Scattered lime slice illustrations">
        <circle class="fruit" cx="210" cy="272" r="26"/><circle class="fruit" cx="305" cy="265" r="48"/>
        <circle class="fruit" cx="420" cy="288" r="30"/><circle class="fruit" cx="598" cy="275" r="45"/>
        <circle class="fruit" cx="414" cy="376" r="22"/><circle class="fruit" cx="424" cy="486" r="35"/>
        <circle class="fruit" cx="775" cy="414" r="30"/><circle class="fruit" cx="706" cy="452" r="24"/>
        <circle class="fruit" cx="485" cy="543" r="24"/><circle class="fruit" cx="721" cy="553" r="42"/>
        <circle class="fruit" cx="346" cy="563" r="28"/><circle class="fruit" cx="908" cy="267" r="45"/>
        <circle class="fruit" cx="953" cy="558" r="28"/><circle class="fruit" cx="824" cy="548" r="20"/>
      </g>
    </g>
    <rect class="guide-line" x="183" y="219" width="828" height="456"/>
    <rect class="guide-thin" x="187" y="226" width="806" height="442"/>
    <rect class="guide-line" x="397" y="183" width="401" height="503"/>
    <line class="guide-dash" x1="159" y1="272" x2="1036" y2="272"/>
    <line class="guide-line" x1="111" y1="222" x2="158" y2="222"/><line class="guide-line" x1="111" y1="227" x2="158" y2="227"/>
    <line class="guide-line" x1="1026" y1="222" x2="1073" y2="222"/><line class="guide-line" x1="1026" y1="227" x2="1073" y2="227"/>
    <line class="guide-line" x1="113" y1="668" x2="160" y2="668"/><line class="guide-line" x1="113" y1="673" x2="160" y2="673"/>
    <line class="guide-line" x1="1031" y1="668" x2="1078" y2="668"/><line class="guide-line" x1="1031" y1="673" x2="1078" y2="673"/>
    <line class="guide-line" x1="185" y1="159" x2="185" y2="214"/><line class="guide-thin" x1="190" y1="159" x2="190" y2="702"/>
    <line class="guide-line" x1="991" y1="159" x2="991" y2="214"/><line class="guide-thin" x1="993" y1="159" x2="993" y2="702"/>
    <line class="guide-line" x1="187" y1="682" x2="187" y2="724"/><line class="guide-line" x1="1010" y1="682" x2="1010" y2="724"/>
    <line class="guide-line" x1="189" y1="701" x2="1008" y2="701"/>
    <path class="guide-line" d="M194 697 L189 701 L194 705 M1003 697 L1008 701 L1003 705"/>
    <line class="guide-line" x1="1045" y1="173" x2="1004" y2="221"/><circle cx="1045" cy="173" r="2.2" fill="var(--guide)"/>
    <path class="guide-line" d="M1004 221 l7 -2 M1004 221 l1 -7"/>
  </svg>
  <h1 class="template-title">109 mm LF_4.875”_Template</h1>
  <span class="guide-text" style="left:162px;top:142px">1 mm clear</span>
  <span class="guide-text" style="left:972px;top:142px">5 mm clear</span>
  <div class="transitional"><strong>Transitional Area</strong><span>(transitions from sidewall to neck)</span></div>
  <span class="guide-text" style="left:577px;top:160px">109 mm LF</span>
  <span class="guide-text" style="left:47px;top:218px">2 mm clear</span>
  <span class="guide-text" style="left:1079px;top:218px">2 mm clear</span>
  <span class="guide-text" style="left:49px;top:665px">2 mm clear</span>
  <span class="guide-text" style="left:1084px;top:665px">2 mm clear</span>
  <span class="guide-text" style="left:1030px;top:419px;font-size:12px;line-height:15px">4.875” Cut Height<br>123.825 MM</span>
  <div class="dim-label" style="top:694px">225 MM SLIT WIDTH<br>8.8583”</div>
  <span class="guide-text centered" style="left:183px;top:735px;font-size:8.5px">1mm Bkgd Bleed<br>Overlap</span>
  <span class="guide-text centered" style="left:905px;top:718px;font-size:8.5px">2mm Bkgd Only<br>No Text/Art</span>

  <p class="back-copy">Lorem ipsum dolor sit amet, consectetuer<br>adipiscing elit. Aenean commodo ligula<br>eget dolor. Aenean massa. Cum sociis<br>natoque penatibus et magnis dis parturient<br>montes, nascetur ridiculus mus. Donec<br>quam felis, ultricies nec, pellentesque eu,<br>pretium quis, sem. Nulla consequat massa<br>quis enim. Donec pede justo, fringilla vel,<br>aliquet nec, vulputate eget, arcu. In enim<br>justo, rhoncus ut, imperdiet a, venenatis<br>vitae, justo. Nullam dictum felis eu pede<br>mollis pretium. Integer tincidunt. Cras<br>dapibus. Vivamus elementum semper nisi.<br>Aenean vulputate eleifend tellus. Aenean<br>leo ligula, porttitor eu, consequat vitae,<br>eleifend ac, enim. Aliquam lorem ante,<br>dapibus in, viverra quis, feugiat a, tellus.<br>Phasellus viverra nulla ut metus varius<br>laoreet. Quisque rutrum. Aenean imperdiet.<br>Etiam ultricies nisi vel augue. Curabitur<br>ullamcorper ultricies nisi. Nam eget dui.</p>
  <div class="brand-name">Briskly</div>
  <div class="product-name">SPARKLING<br>WATER</div>
  <div class="divider"></div>
  <div class="claims">NATURAL FLAVORS<br>&amp; B-VITAMINS</div>
  <div class="flavor-pill">LIME</div>
  <div class="volume">12oz</div>

  <div class="claim-icon" style="top:295px"><b>0</b><small>SUGAR</small></div>
  <div class="claim-icon" style="top:327px"><b>0</b><small>CALORIES</small></div>
  <div class="claim-icon" style="top:361px"><b>0</b><small>SODIUM</small></div>
  <div class="claim-icon claim-icon--word" style="top:395px">B6 &amp;<br>B12</div>
  <div class="claim-icon claim-icon--word" style="top:430px">NON<br>GMO</div>
  <div class="claim-icon claim-icon--word" style="top:461px">GLUTEN<br>FREE</div>
  <div class="claim-icon claim-icon--word claim-icon--single" style="top:498px">VEGAN</div>
  <svg class="artwork overlay" viewBox="0 0 1200 773" aria-hidden="true">
    <rect class="panel-box" x="852" y="314" width="79" height="154"/>
    <rect class="panel-box" x="934" y="395" width="46" height="73"/>
    <text class="panel-caption" transform="translate(959 445) rotate(-90)">BARCODE</text>
  </svg>
  <span class="nutrition-label">NUTRITION PANEL</span>
  <div class="boost">BOOST<br>IMMUNITY</div>
</section>

<!-- ===== Mango ===== -->
<section class="template template--mango">
  <svg class="artwork" viewBox="0 0 1200 773">
    <defs>
      <clipPath id="clip-mango"><rect x="183" y="219" width="828" height="456"/><rect x="397" y="183" width="401" height="503"/></clipPath>
    </defs>
    <g clip-path="url(#clip-mango)">
      <rect class="bg" x="183" y="183" width="828" height="503"/>
      <path class="wave-1" d="M183 540 C250 522 320 548 400 534 S560 518 640 536 S820 518 1011 532 V686 H183Z"/>
      <path class="wave-2" d="M183 566 C260 556 330 576 420 564 S580 552 660 570 S830 554 1011 564 V586 C830 578 660 594 560 584 S330 594 183 588Z"/>
      <path class="wave-2" d="M183 606 C260 598 350 616 440 604 S610 594 700 610 S850 596 1011 606 V628 C850 620 700 634 600 624 S380 632 183 626Z"/>
      <g role="img" aria-label="Scattered mango illustrations">
        <ellipse class="fruit" cx="293" cy="280" rx="38" ry="18"/><ellipse class="fruit" cx="388" cy="273" rx="22" ry="14"/>
        <ellipse class="fruit" cx="421" cy="296" rx="26" ry="30"/><ellipse class="fruit" cx="593" cy="273" rx="40" ry="18"/>
        <ellipse class="fruit" cx="760" cy="285" rx="30" ry="30"/><ellipse class="fruit" cx="772" cy="380" rx="26" ry="26"/>
        <ellipse class="fruit" cx="200" cy="368" rx="16" ry="24"/><ellipse class="fruit" cx="408" cy="443" rx="24" ry="34"/>
        <ellipse class="fruit" cx="474" cy="471" rx="28" ry="24"/><ellipse class="fruit" cx="750" cy="468" rx="18" ry="26"/>
        <ellipse class="fruit" cx="494" cy="550" rx="34" ry="16"/><ellipse class="fruit" cx="696" cy="555" rx="38" ry="52"/>
        <ellipse class="fruit" cx="338" cy="554" rx="26" ry="36"/><ellipse class="fruit" cx="970" cy="560" rx="22" ry="32"/>
        <ellipse class="fruit" cx="884" cy="281" rx="38" ry="18"/><ellipse class="fruit" cx="975" cy="356" rx="16" ry="20"/>
      </g>
    </g>
    <rect class="guide-line" x="183" y="219" width="828" height="456"/>
    <rect class="guide-thin" x="187" y="226" width="806" height="442"/>
    <rect class="guide-line" x="397" y="183" width="401" height="503"/>
    <line class="guide-dash" x1="159" y1="272" x2="1036" y2="272"/>
    <line class="guide-line" x1="111" y1="222" x2="158" y2="222"/><line class="guide-line" x1="111" y1="227" x2="158" y2="227"/>
    <line class="guide-line" x1="1026" y1="222" x2="1073" y2="222"/><line class="guide-line" x1="1026" y1="227" x2="1073" y2="227"/>
    <line class="guide-line" x1="113" y1="668" x2="160" y2="668"/><line class="guide-line" x1="113" y1="673" x2="160" y2="673"/>
    <line class="guide-line" x1="1031" y1="668" x2="1078" y2="668"/><line class="guide-line" x1="1031" y1="673" x2="1078" y2="673"/>
    <line class="guide-line" x1="185" y1="159" x2="185" y2="214"/><line class="guide-thin" x1="190" y1="159" x2="190" y2="702"/>
    <line class="guide-line" x1="991" y1="159" x2="991" y2="214"/><line class="guide-thin" x1="993" y1="159" x2="993" y2="702"/>
    <line class="guide-line" x1="187" y1="682" x2="187" y2="724"/><line class="guide-line" x1="1010" y1="682" x2="1010" y2="724"/>
    <line class="guide-line" x1="189" y1="701" x2="1008" y2="701"/>
    <path class="guide-line" d="M194 697 L189 701 L194 705 M1003 697 L1008 701 L1003 705"/>
    <line class="guide-line" x1="1045" y1="173" x2="1004" y2="221"/><circle cx="1045" cy="173" r="2.2" fill="var(--guide)"/>
    <path class="guide-line" d="M1004 221 l7 -2 M1004 221 l1 -7"/>
  </svg>
  <h1 class="template-title">109 mm LF_4.875”_Template</h1>
  <span class="guide-text" style="left:162px;top:142px">1 mm clear</span>
  <span class="guide-text" style="left:972px;top:142px">5 mm clear</span>
  <div class="transitional"><strong>Transitional Area</strong><span>(transitions from sidewall to neck)</span></div>
  <span class="guide-text" style="left:577px;top:160px">109 mm LF</span>
  <span class="guide-text" style="left:47px;top:218px">2 mm clear</span>
  <span class="guide-text" style="left:1079px;top:218px">2 mm clear</span>
  <span class="guide-text" style="left:49px;top:665px">2 mm clear</span>
  <span class="guide-text" style="left:1084px;top:665px">2 mm clear</span>
  <span class="guide-text" style="left:1030px;top:419px;font-size:12px;line-height:15px">4.875” Cut Height<br>123.825 MM</span>
  <div class="dim-label" style="top:694px">225 MM SLIT WIDTH<br>8.8583”</div>
  <span class="guide-text centered" style="left:183px;top:735px;font-size:8.5px">1mm Bkgd Bleed<br>Overlap</span>
  <span class="guide-text centered" style="left:905px;top:718px;font-size:8.5px">2mm Bkgd Only<br>No Text/Art</span>

  <p class="back-copy">Lorem ipsum dolor sit amet, consectetuer<br>adipiscing elit. Aenean commodo ligula<br>eget dolor. Aenean massa. Cum sociis<br>natoque penatibus et magnis dis parturient<br>montes, nascetur ridiculus mus. Donec<br>quam felis, ultricies nec, pellentesque eu,<br>pretium quis, sem. Nulla consequat massa<br>quis enim. Donec pede justo, fringilla vel,<br>aliquet nec, vulputate eget, arcu. In enim<br>justo, rhoncus ut, imperdiet a, venenatis<br>vitae, justo. Nullam dictum felis eu pede<br>mollis pretium. Integer tincidunt. Cras<br>dapibus. Vivamus elementum semper nisi.<br>Aenean vulputate eleifend tellus. Aenean<br>leo ligula, porttitor eu, consequat vitae,<br>eleifend ac, enim. Aliquam lorem ante,<br>dapibus in, viverra quis, feugiat a, tellus.<br>Phasellus viverra nulla ut metus varius<br>laoreet. Quisque rutrum. Aenean imperdiet.<br>Etiam ultricies nisi vel augue. Curabitur<br>ullamcorper ultricies nisi. Nam eget dui.</p>
  <div class="brand-name">Briskly</div>
  <div class="product-name">SPARKLING<br>WATER</div>
  <div class="divider"></div>
  <div class="claims">NATURAL FLAVORS<br>&amp; B-VITAMINS</div>
  <div class="flavor-pill">MANGO</div>
  <div class="volume" style="color:#8a6a12">12oz</div>

  <div class="claim-icon" style="top:295px"><b>0</b><small>SUGAR</small></div>
  <div class="claim-icon" style="top:327px"><b>0</b><small>CALORIES</small></div>
  <div class="claim-icon" style="top:361px"><b>0</b><small>SODIUM</small></div>
  <div class="claim-icon claim-icon--word" style="top:395px">B6 &amp;<br>B12</div>
  <div class="claim-icon claim-icon--word" style="top:430px">NON<br>GMO</div>
  <div class="claim-icon claim-icon--word" style="top:461px">GLUTEN<br>FREE</div>
  <div class="claim-icon claim-icon--word claim-icon--single" style="top:498px">VEGAN</div>
  <svg class="artwork overlay" viewBox="0 0 1200 773" aria-hidden="true">
    <rect class="panel-box" x="852" y="314" width="79" height="154"/>
    <rect class="panel-box" x="934" y="395" width="46" height="73"/>
    <text class="panel-caption" transform="translate(959 445) rotate(-90)">BARCODE</text>
  </svg>
  <span class="nutrition-label">NUTRITION PANEL</span>
  <div class="boost">BOOST<br>IMMUNITY</div>
</section>

</body>
</html>
```